business card

Business card for new business.
Red and black corporate colors.
Card can have an Indsutrial feel to it. Feel free to add Rust, Bolted steel, or graphics as you see fit. We provide highly specialized services to the below mentioned industries.
Keep information out of corners so that if I want I can choose rounded corners.
Information
- front. name - title - phone - email
- Rear
Forging - Ports - Pipelines - Quarrying - Utilities
Halden - Brookmere - Port Ashby - Carrow Falls - Westmark

```html
<!DOCTYPE html>
<html lang="en">
<head>
<meta charset="utf-8">
<title>Ferroline Business Card</title>
<link href="https://fonts.googleapis.com/css2?family=Roboto:wght@400;500&family=Roboto+Condensed:wght@700&display=swap" rel="stylesheet">
<style>
  :root {
    --backdrop: #2b2b2b;
    --steel-light: #f4f4f4;
    --steel-mid: #e4e4e4;
    --steel-dark: #cdcdcd;
    --brush-line: rgba(120,120,120,0.10);
    --brand-red: #e2001a;
    --ink-gray: #7a7a7a;
    --text-gray: #555555;
    --divider: #b8b8b8;
  }
  html, body {
    margin: 0;
    padding: 0;
    width: 1200px;
    height: 960px;
    overflow: hidden;
    background: var(--backdrop);
  }
  .stage {
    position: relative;
    width: 1200px;
    height: 960px;
  }
  .card {
    position: absolute;
    width: 600px;
    height: 343px;
    background:
      repeating-linear-gradient(90deg, transparent 0, transparent 3px, var(--brush-line) 3px, var(--brush-line) 4px, transparent 4px, transparent 9px),
      linear-gradient(90deg, var(--steel-dark) 0%, var(--steel-light) 30%, var(--steel-mid) 55%, var(--steel-light) 75%, var(--steel-dark) 100%);
    box-shadow: 0 3px 8px rgba(0,0,0,0.5);
    font-family: "Roboto", Arial, sans-serif;
  }
  .card--front { left: 314px; top: 113px; }
  .card--back { left: 311px; top: 472px; }

  .brand-name {
    position: absolute;
    font-family: "Roboto Condensed", "Arial Narrow", sans-serif;
    font-weight: 700;
    line-height: 1;
    margin: 0;
    letter-spacing: 0.5px;
  }
  .card--front .brand-name {
    left: 86px;
    top: 148px;
    font-size: 50px;
    color: var(--ink-gray);
  }
  .divider {
    position: absolute;
    left: 347px;
    top: 115px;
    width: 2px;
    height: 114px;
    background: var(--divider);
  }
  .contact-block {
    position: absolute;
    left: 372px;
    top: 114px;
  }
  .person-name {
    margin: 0;
    font-family: "Roboto Condensed", "Arial Narrow", sans-serif;
    font-weight: 700;
    font-size: 23px;
    line-height: 1;
    color: var(--brand-red);
  }
  .person-title {
    margin: 5px 0 10px;
    font-size: 15px;
    color: var(--ink-gray);
    line-height: 1.1;
  }
  .contact-list {
    list-style: none;
    margin: 0;
    padding: 0;
  }
  .contact-item {
    display: flex;
    align-items: center;
    font-size: 14.5px;
    color: var(--text-gray);
    height: 19.5px;
  }
  .contact-icon {
    width: 12px;
    height: 12px;
    margin-right: 11px;
    fill: var(--brand-red);
  }

  .card--back .brand-name {
    left: 0;
    width: 600px;
    text-align: center;
    top: 118px;
    font-size: 66px;
    color: var(--brand-red);
  }
  .services {
    position: absolute;
    left: 0;
    top: 257px;
    width: 600px;
    margin: 0;
    text-align: center;
    font-size: 14.5px;
    line-height: 18px;
    color: var(--text-gray);
  }
  .bullet { color: var(--brand-red); }
</style>
</head>
<body>
<div class="stage">
  <section class="card card--front">
    <p class="brand-name">FERROLINE</p>
    <div class="divider"></div>
    <div class="contact-block">
      <h1 class="person-name">OWEN HARTLEY</h1>
      <p class="person-title">CEO/FOUNDER</p>
      <ul class="contact-list">
        <li class="contact-item">
          <svg class="contact-icon" viewBox="0 0 24 24" aria-hidden="true"><path d="M6.6 10.8a15.1 15.1 0 0 0 6.6 6.6l2.2-2.2c.3-.3.7-.4 1-.2 1.1.4 2.3.6 3.6.6.6 0 1 .4 1 1V20c0 .6-.4 1-1 1A17 17 0 0 1 3 4c0-.6.4-1 1-1h3.5c.6 0 1 .4 1 1 0 1.3.2 2.5.6 3.6.1.3 0 .7-.2 1z"/></svg>
          555 210 4873
        </li>
        <li class="contact-item">
          <svg class="contact-icon" viewBox="0 0 24 24" aria-hidden="true"><path d="M2 5h20v14H2z"/><path d="M3 6l9 6.5L21 6" fill="none" stroke="#fff" stroke-width="1.8"/></svg>
          info@ferroline.com
        </li>
        <li class="contact-item">
          <svg class="contact-icon" viewBox="0 0 24 24" aria-hidden="true"><circle cx="12" cy="12" r="10"/></svg>
          www.ferroline.com
        </li>
      </ul>
    </div>
  </section>

  <section class="card card--back">
    <p class="brand-name">FERROLINE</p>
    <p class="services">
      Forging <span class="bullet">•</span> Ports <span class="bullet">•</span> Pipelines <span class="bullet">•</span> Quarrying<br>
      Utilities <span class="bullet">•</span> Halden <span class="bullet">•</span> Brookmere <span class="bullet">•</span> Port Ashby<br>
      Carrow Falls <span class="bullet">•</span> Westmark
    </p>
  </section>
</div>
</body>
</html>
```